High value cover design for an A4 ideation pad.

The product is NOT A BOOK.

It's an A4 ideation pad for professionals, designers and creators who handwrite their ideas. Visualise creators like Milo Varnet, Owen Plaskit and Gregor Lunwick in your mind's eye.

I'm looking for a cover design for the ideation pad. Both front and back.

It should look, feel and convey the following.

--> A handcrafted product experience

--> High value & Elegance

--> Inspiration

Mandatory --> See Uploaded Files --> Files 1, 5 & 6

Target Market(s)

- Designers

-Creative Professionals

- Entrepreneurs

who handwrite their ideas. Visualise creators like Milo Varnet, Owen Plaskit and Gregor Lunwick in your mind's eye.

Industry/Entity Type

Stationary

Font styles to use
Script
Other font styles liked:
• Calligraphy

Colors
fbed22

Requirements
Must have
• Title text - Quiet Kettle Notes

-Text in gold on brown leather background to convey high value for the front cover.

--> High value & Elegance

--> Inspiration

--> Should compel the customers to pick up and own the idea pad
Nice to have
• That's my take but other ideas are welcome
Should not have
• Must not convey

- low value

```html
<!DOCTYPE html>
<html lang="en">
<head>
<meta charset="utf-8">
<title>Quiet Kettle Notes — Ideation Pad Cover</title>
<link rel="stylesheet" href="https://fonts.googleapis.com/css2?family=Pinyon+Script&display=swap">
<style>
  :root {
    --page: #ffffff;
    --cover-black: #000000;
    --ornament-gold: #6b4f12;
    --gold-light: #fff3b0;
    --gold-mid: #e2c15a;
    --gold-deep: #a9841f;
    --gold-shadow: #8a6a18;
    --title-gold-1: #f6d25a;
    --title-gold-2: #b8860b;
    --title-gold-3: #7a5208;
  }
  * { margin: 0; padding: 0; box-sizing: border-box; }
  html, body {
    width: 1200px;
    height: 853px;
    overflow: hidden;
    background: var(--page);
  }
  .spread {
    position: relative;
    width: 1200px;
    height: 853px;
  }
  .cover {
    position: absolute;
    top: 30px;
    width: 570px;
    height: 802px;
    background: linear-gradient(135deg, var(--gold-deep), var(--gold-light) 30%, var(--gold-mid) 55%, var(--gold-light) 80%, var(--gold-shadow));
    padding: 8px;
  }
  .cover--front { left: 15px; }
  .cover--back { left: 598px; width: 568px; }
  .cover__bevel {
    width: 100%;
    height: 100%;
    padding: 10px;
    background: linear-gradient(315deg, var(--gold-deep), var(--gold-light) 35%, var(--gold-mid) 60%, var(--gold-light));
    border: 1px solid var(--gold-shadow);
  }
  .cover__panel {
    position: relative;
    width: 100%;
    height: 100%;
    border: 2px solid var(--gold-light);
    background: var(--cover-black);
    overflow: hidden;
  }
  .cover__ornament {
    position: absolute;
    inset: 0;
    background:
      radial-gradient(ellipse 62% 70% at 50% 50%, var(--cover-black) 60%, transparent 100%),
      linear-gradient(90deg, var(--ornament-gold), var(--cover-black) 22%, var(--cover-black) 78%, var(--ornament-gold));
  }
  .cover--front .cover__ornament {
    background:
      radial-gradient(ellipse 58% 68% at 42% 48%, var(--cover-black) 62%, transparent 100%),
      linear-gradient(90deg, #3a2b0a, var(--cover-black) 14%, var(--cover-black) 72%, var(--ornament-gold));
  }
  .cover__title {
    position: absolute;
    left: 150px;
    top: 292px;
    width: 230px;
    font-family: "Pinyon Script", cursive;
    font-weight: 400;
    font-size: 62px;
    line-height: 66px;
    text-align: center;
    background: linear-gradient(180deg, var(--title-gold-1), var(--title-gold-2) 55%, var(--title-gold-3));
    -webkit-background-clip: text;
    background-clip: text;
    color: transparent;
  }
  .cover__title span { display: block; }
</style>
</head>
<body>
  <main class="spread">
    <section class="cover cover--front">
      <div class="cover__bevel">
        <div class="cover__panel">
          <div class="cover__ornament" role="img" aria-label="Flowing gold line ornaments with spirals along the sides of the front cover"></div>
          <h1 class="cover__title"><span>Quiet</span><span>Kettle</span><span>Notes</span></h1>
        </div>
      </div>
    </section>
    <section class="cover cover--back">
      <div class="cover__bevel">
        <div class="cover__panel">
          <div class="cover__ornament" role="img" aria-label="Flowing gold line ornaments with spirals framing the back cover"></div>
        </div>
      </div>
    </section>
  </main>
</body>
</html>
```